Design the Business card for NetVaultic

Business card required for a professional Cyber Security business.
Company Logo and Icon has already been provided however I would like other options for the logo and icon to compare to. Alternatively, please refine/enhance the image of the logo.icon I have already provided.

If you are going to use the provided logo and icon, I was thinking that the company raised Logo on White background would serve well on the front of the card. See attached. AND, a large company raised stand-alone icon to appear on black background on the back of the card with tagline 'Cyber Risk Management, Governance and Consulting' or 'Cyber Security for your Business' See attached.
Alternatively, provide your own design for the logo and icon.

Target Market(s)

Enterprise, Government, Financial.

Contact Information for Business Card

Tavin Orloweth
Founder and CEO

Email Address
Mobile Number
Website URL
LinkedIn URL

Logo Text

NetVaultic - see attached example of logo

Font styles to use
Other font styles liked:
• Berlin Sans FB

Requirements
Must have
• Clean large and bold icon on the back with tagline.
• Horizontal alignment,
Nice to have
• Round edges.
• Raised Logo/Icon
Should not have
• An unprofessional look and feel.

```html
<!DOCTYPE html>
<html lang="en">
<head>
<meta charset="utf-8">
<title>NetVaultic Business Card</title>
<link href="https://fonts.googleapis.com/css2?family=Overlock:wght@400;700;900&display=swap" rel="stylesheet">
<style>
  :root {
    --backdrop: #1f2022;
    --card-light: #f1f1f1;
    --card-dark: #1b1c1e;
    --brand-blue: #1673c6;
    --accent-blue: #4a78c8;
    --rule-blue: #3f63c8;
    --brand-yellow: #f5b800;
    --text-grey: #555658;
  }
  * { margin: 0; padding: 0; box-sizing: border-box; }
  html, body {
    width: 1200px; height: 960px; overflow: hidden;
    background: var(--backdrop);
    font-family: "Overlock", "Trebuchet MS", sans-serif;
  }
  .canvas { position: relative; width: 1200px; height: 960px; }

  .card-front {
    position: absolute; left: 322px; top: 108px; width: 600px; height: 342px;
    background: var(--card-light);
  }
  .rule { position: absolute; left: 20px; width: 562px; height: 14px; }
  .rule--top { top: 14px; }
  .rule--bottom { top: 315px; }

  .contact-block {
    position: absolute; left: 0; right: 0; top: 100px; text-align: center;
  }
  .person-name {
    color: var(--brand-blue); font-weight: 700; font-size: 22px;
    letter-spacing: 0.3px; line-height: 28px;
  }
  .person-title {
    color: var(--brand-yellow); font-weight: 700; font-size: 14px;
    line-height: 18px; margin-bottom: 16px;
  }
  .contact-line {
    color: var(--text-grey); font-weight: 700; font-size: 13px; line-height: 19px;
  }
  .social-dot {
    display: inline-block; width: 13px; height: 13px; border-radius: 50%;
    background: var(--brand-blue); vertical-align: -2px; margin-right: 6px;
  }

  .card-back {
    position: absolute; left: 322px; top: 494px; width: 596px; height: 340px;
    background: var(--card-dark); border-radius: 16px;
  }
  .brand-lockup {
    position: absolute; left: 122px; top: 116px; display: flex; align-items: center;
  }
  .brand-mark {
    width: 82px; height: 82px; border-radius: 50%; background: var(--brand-blue);
    margin-right: 12px;
  }
  .brand-name {
    color: var(--brand-blue); font-weight: 700; font-size: 48px; line-height: 1;
  }
  .tagline {
    position: absolute; left: 0; right: 0; top: 274px; text-align: center;
    font-size: 18px; font-weight: 700;
  }
  .tagline__lead { color: var(--accent-blue); }
  .tagline__tail { color: var(--brand-yellow); }
</style>
</head>
<body>
<main class="canvas">
  <section class="card-front">
    <svg class="rule rule--top" viewBox="0 0 562 14">
      <line x1="11" y1="7" x2="551" y2="7" stroke="#3f63c8" stroke-width="1.5"/>
      <circle cx="6" cy="7" r="5" fill="#f1f1f1" stroke="#3f63c8" stroke-width="1.2"/>
      <circle cx="556" cy="7" r="5" fill="#f1f1f1" stroke="#3f63c8" stroke-width="1.2"/>
    </svg>
    <div class="contact-block">
      <p class="person-name">TAVIN ORLOWETH</p>
      <p class="person-title">FOUNDER &amp; CEO</p>
      <p class="contact-line">(P) 555 214 0873</p>
      <p class="contact-line">(E) tavin@netvaultic.com</p>
      <p class="contact-line">www.netvaultic.com</p>
      <p class="contact-line"><span class="social-dot"></span>netvaultic</p>
    </div>
    <svg class="rule rule--bottom" viewBox="0 0 562 14">
      <line x1="11" y1="7" x2="551" y2="7" stroke="#3f63c8" stroke-width="1.5"/>
      <circle cx="6" cy="7" r="5" fill="#f1f1f1" stroke="#3f63c8" stroke-width="1.2"/>
      <circle cx="556" cy="7" r="5" fill="#f1f1f1" stroke="#3f63c8" stroke-width="1.2"/>
    </svg>
  </section>

  <section class="card-back">
    <div class="brand-lockup">
      <span class="brand-mark"></span>
      <span class="brand-name">NetVaultic</span>
    </div>
    <p class="tagline">
      <span class="tagline__lead">Cyber Risk Management,</span>
      <span class="tagline__tail">Governance &amp; Consulting</span>
    </p>
  </section>
</main>
</body>
</html>
```